Fitness Equipment & Service

I want to make the card eye catching and fun. We are called Corvane Motion Limited and we are based in Wales. We sell, install and service all types of fitness equipment from Skipping ropes, right through the Dumbbells, Kettle bells and Barbells through to state of the art Treadmills, Running Machines and Strength Equipment. We also design and install changing room furniture and lockers.

TYPOGRAPHY
We would like to use Futrura. Futura has an appearance of efficiency and forwardness. The typeface is derived
from simple geometric forms (near-perfect circles, triangles and squares) and is based on strokes of
near-even weight, which are low in contrast. This is most visible in the almost perfectly round stroke of
the o, which is nonetheless slightly ovoid.
The lowercase has tall ascenders, which rise above the cap line. The uppercase
characters present proportions similar to those of classical Roman capitals.

TYPOGRAPHIC CONSIDERATIONS
No Strike though
No Horizontal Scaling
No Drop Shadows
No Effects
Never use less than 120% Leading

OUR CORPORATE COLOURS
BRAND GUIDELINES
We were thinking that our primary colour palette consists of the Acid Green (Pantone 382) and Process Black.

We work closely with tquarly Ltd and would like to include their name on the card somewhere. I have attached images of the other brands that we work with as an idea or the small icons I have included that illustrate what we do?. I have very kindly been given permission to use any of the images off the files that I have included below, so I hope these help. I will include these below. I would be open to suggestions if it made the card more striking Can you do it?
Updates

Hi All, Just wanted to add a few thoughts but you are the guys with the creative visions (thats why are here) We are based in Wales, UK and we would be open to lots of different ideas on a theme but must be eye catching, Bold and FUN. If you can or think that the Welsh or any dragon could be put in there then go for it (its not a must have) We have also added some ideas for colour but again its over to you!! GO FOR IT ! Thanks and look forward to your visions! Owen

Hi All, Just thought I would sen through the contact details that need to be on the card. (if you want to play around with icons instead of the wording twitter, Facebook, go for it): Corvane Motion Limited Owen Pritchard Managing Director Mob: +44 (0)7582 913 406 e-mail: sales@corvanemotion.co.uk Web: Corvanemotion.co.uk twitter: @motionLetterbin Facebook: Corvane Motion Limited

```html
<!DOCTYPE html>
<html lang="en">
<head>
<meta charset="utf-8">
<title>Corvane Motion Limited – Business Card</title>
<link rel="stylesheet" href="https://fonts.googleapis.com/css2?family=Open+Sans:wght@400;700&display=swap">
<style>
  :root {
    --page-bg: #e9e6e1;
    --navy-deep: #1b2f6b;
    --navy-mid: #1f4a9c;
    --navy-light: #2a66c0;
    --ink-navy: #121a3a;
    --gold: #d8a739;
    --gold-dark: #a97a1f;
    --white: #ffffff;
    --map-grey: #ececec;
  }
  * { margin: 0; padding: 0; box-sizing: border-box; }
  html, body {
    width: 1200px; height: 1000px; overflow: hidden;
    background: var(--page-bg);
    font-family: "Open Sans", Arial, sans-serif;
  }
  .card {
    position: absolute; left: 265px; width: 666px; height: 397px;
    overflow: hidden;
    box-shadow: 0 6px 14px rgba(0,0,0,0.25);
  }
  .card--front { top: 73px; background: var(--white); }
  .card--back {
    top: 532px;
    background: radial-gradient(ellipse at 50% 45%, var(--navy-light) 0%, var(--navy-mid) 35%, var(--navy-deep) 80%);
  }
  .card__shapes { position: absolute; inset: 0; }
  .world-map {
    position: absolute;
    border-radius: 40px;
  }
  .world-map--front {
    left: 330px; top: 30px; width: 320px; height: 300px;
    background: radial-gradient(ellipse at 50% 50%, var(--map-grey) 0%, rgba(236,236,236,0) 70%);
  }
  .world-map--back {
    left: 40px; top: 30px; width: 590px; height: 300px;
    background: radial-gradient(ellipse at 50% 50%, rgba(255,255,255,0.08) 0%, rgba(255,255,255,0) 70%);
  }
  .contact {
    position: absolute; left: 33px; top: 74px; color: var(--white);
  }
  .contact__name { font-size: 20px; font-weight: 700; letter-spacing: 0.5px; line-height: 1.3; }
  .contact__role { font-size: 14.5px; line-height: 1.3; margin-bottom: 30px; }
  .contact__row {
    display: flex; align-items: center; gap: 8px;
    font-size: 15px; line-height: 1.6;
  }
  .contact__icon { width: 14px; height: 14px; flex: none; }
  .contact__partner { font-size: 15px; font-weight: 700; margin: 14px 0 12px; line-height: 1.3; }
  .contact__dot { width: 10px; height: 10px; border-radius: 50%; background: var(--white); margin: 0 2px; flex: none; }
  .brand {
    position: absolute; display: flex; flex-direction: column; align-items: center; gap: 22px;
  }
  .brand--front { left: 400px; top: 86px; width: 230px; }
  .brand--back { left: 183px; top: 68px; width: 300px; }
  .brand__circle { border-radius: 50%; }
  .brand--front .brand__circle { width: 120px; height: 120px; background: var(--navy-deep); }
  .brand--back .brand__circle { width: 150px; height: 150px; background: var(--gold); }
  .brand__name {
    font-weight: 700; text-align: center; line-height: 1.2; letter-spacing: 0.5px;
  }
  .brand--front .brand__name { font-size: 22px; color: var(--ink-navy); }
  .brand--back .brand__name { font-size: 28px; color: var(--white); }
</style>
</head>
<body>

<section class="card card--front">
  <div class="world-map world-map--front" role="img" aria-label="Faint grey world map background"></div>
  <svg class="card__shapes" width="666" height="397" viewBox="0 0 666 397">
    <defs>
      <radialGradient id="front-blue" cx="0.4" cy="0.45" r="0.7">
        <stop offset="0" stop-color="#2a66c0"/>
        <stop offset="0.5" stop-color="#1f4a9c"/>
        <stop offset="1" stop-color="#1b2f6b"/>
      </radialGradient>
    </defs>
    <polygon points="405,0 438,0 318,200 448,397 415,397 300,200" fill="var(--gold)"/>
    <polygon points="420,0 428,0 310,200 433,397 425,397 304,200" fill="var(--gold-dark)"/>
    <polygon points="0,0 405,0 300,200 415,397 0,397" fill="url(#front-blue)"/>
  </svg>
  <div class="contact">
    <p class="contact__name">OWEN PRITCHARD</p>
    <p class="contact__role">Managing Director</p>
    <p class="contact__row">
      <svg class="contact__icon" viewBox="0 0 14 14"><rect x="3.5" y="0.8" width="7" height="12.4" rx="1.2" fill="none" stroke="#fff" stroke-width="1.3"/><circle cx="7" cy="11" r="0.8" fill="#fff"/></svg>
      +44 (0)7582 913 406
    </p>
    <p class="contact__row">
      <svg class="contact__icon" viewBox="0 0 14 14"><rect x="0.5" y="3" width="13" height="8.5" fill="#fff"/><polyline points="0.5,3 7,8 13.5,3" fill="none" stroke="#1f4a9c" stroke-width="1.2"/></svg>
      sales@corvanemotion.co.uk
    </p>
    <p class="contact__row">
      <svg class="contact__icon" viewBox="0 0 14 14"><rect x="0.8" y="1.5" width="12.4" height="8.5" fill="none" stroke="#fff" stroke-width="1.3"/><rect x="4" y="11.5" width="6" height="1.3" fill="#fff"/></svg>
      Corvanemotion.co.uk
    </p>
    <p class="contact__partner">tquarly Ltd</p>
    <p class="contact__row"><span class="contact__dot"></span>@motionLetterbin</p>
    <p class="contact__row"><span class="contact__dot"></span>Corvane Motion Limited</p>
  </div>
  <div class="brand brand--front">
    <div class="brand__circle"></div>
    <p class="brand__name">Corvane Motion Limited</p>
  </div>
</section>

<section class="card card--back">
  <div class="world-map world-map--back" role="img" aria-label="Faint world map across the card background"></div>
  <div class="brand brand--back">
    <div class="brand__circle"></div>
    <p class="brand__name">Corvane Motion Limited</p>
  </div>
</section>

</body>
</html>
```